New business stationairy

I need paper with header and footer and business cards.
I am a Ltd Company and my main field of expertise is QA/QC inspection in the Oil and Gas Industry. I will need all contact detail inserted and a footer with registration number and bank details etc

```html
<!DOCTYPE html>
<html lang="en">
<head>
<meta charset="utf-8">
<title>Halvorsen Verification Services Ltd — Business Card</title>
<link rel="stylesheet" href="https://fonts.googleapis.com/css2?family=Questrial&family=Open+Sans:wght@400;600;700&display=swap">
<style>
  :root {
    --page-bg: #e6e8ec;
    --card-white: #fbfbfa;
    --brand-blue: #1c6fb8;
    --brand-navy: #1d3f8f;
    --back-light: #1f88c9;
    --back-dark: #23409a;
    --text-grey: #4a4d52;
    --label-blue: #1a8ac6;
    --ghost: rgba(255, 255, 255, 0.14);
    --white: #ffffff;
  }

  * { margin: 0; padding: 0; box-sizing: border-box; }

  html, body {
    width: 1200px;
    height: 800px;
    overflow: hidden;
    background: var(--page-bg);
  }

  .canvas {
    position: relative;
    width: 1200px;
    height: 800px;
    display: flex;
    flex-direction: column;
    align-items: center;
    justify-content: center;
    gap: 50px;
  }

  .card {
    position: relative;
    width: 560px;
    height: 320px;
    box-shadow: 0 10px 28px rgba(20, 30, 60, 0.18);
    overflow: hidden;
  }

  /* Front */
  .card--front {
    background: var(--card-white);
    font-family: "Questrial", sans-serif;
    text-align: center;
  }

  .brand {
    position: absolute;
    top: 46px;
    left: 0;
    right: 0;
    display: flex;
    flex-direction: column;
    align-items: center;
  }

  .brand__dot {
    width: 62px;
    height: 62px;
    border-radius: 50%;
    background: var(--brand-blue);
    margin-bottom: 16px;
  }

  .brand__name {
    font-family: "Questrial", sans-serif;
    font-size: 42px;
    letter-spacing: 4px;
    color: var(--brand-blue);
    line-height: 1;
  }

  .brand__sub {
    font-family: "Questrial", sans-serif;
    font-size: 13px;
    letter-spacing: 1px;
    color: var(--brand-blue);
    margin-top: 6px;
  }

  .contact {
    position: absolute;
    left: 0;
    right: 0;
    bottom: 40px;
    font-size: 13px;
    color: var(--text-grey);
    line-height: 1.5;
  }

  .contact__label {
    font-family: "Open Sans", sans-serif;
    font-weight: 700;
    color: var(--label-blue);
  }

  /* Back */
  .card--back {
    background: linear-gradient(120deg, var(--back-light) 0%, var(--back-dark) 100%);
    font-family: "Open Sans", sans-serif;
    color: var(--white);
  }

  .back__ghost-name {
    position: absolute;
    top: 118px;
    left: 150px;
    font-family: "Questrial", sans-serif;
    font-size: 52px;
    letter-spacing: 5px;
    color: var(--ghost);
    line-height: 1;
  }

  .back__ghost-sub {
    position: absolute;
    top: 176px;
    left: 296px;
    font-family: "Questrial", sans-serif;
    font-size: 13px;
    letter-spacing: 1px;
    color: var(--ghost);
  }

  .holder {
    position: absolute;
    right: 34px;
    bottom: 30px;
    text-align: right;
  }

  .holder__name {
    font-weight: 700;
    font-size: 20px;
    letter-spacing: 0.5px;
  }

  .holder__role {
    font-weight: 400;
    font-size: 15px;
    opacity: 0.9;
  }
</style>
</head>
<body>
  <main class="canvas">
    <section class="card card--front" aria-label="Business card front">
      <div class="brand">
        <span class="brand__dot" aria-hidden="true"></span>
        <span class="brand__name">HALVORSEN</span>
        <span class="brand__sub">VERIFICATION SERVICES LTD</span>
      </div>
      <address class="contact" style="font-style: normal;">
        The Willows, Mill Lane, Ashcombe, Oakfield, Dorset<br>
        <span class="contact__label">Phone:</span> +07700 900417 ·
        <span class="contact__label">Email:</span> maren@halvorsenvs.co.uk
      </address>
    </section>

    <section class="card card--back" aria-label="Business card back">
      <span class="back__ghost-name" aria-hidden="true">HALVORSEN</span>
      <span class="back__ghost-sub" aria-hidden="true">VERIFICATION SERVICES LTD</span>
      <div class="holder">
        <p class="holder__name">MAREN HALVORSEN</p>
        <p class="holder__role">Managing Director</p>
      </div>
    </section>
  </main>
</body>
</html>
```